Website improvements and Adding Functionalities at https://mervo.site/tarnovex

1.Search functionality
2.Payment process functionality
3. Application configuration
4. Registration functionality activation
5. Chat functionality
6.Language switching functionality (Portuguese & French)
7.Bespoke interactive modules
8. Automated web scraping and data synchronisation mechanisms
9. News Page
10.Webinar facilities
11. Basic SEO optimisation
12. Speed and performance optimisation
13. Security configuration
14. Google Analytics integration
15. Cross-browser and mobile testing
16. Website deployment and launch support

Target Market(s)

My target markets are companies, investors, suppliers and professionals with an interest in the Mozambican oil and gas sector

Industry/Entity Type

Oil and Gas

Coding

Coded - Design and coding required

Number of Pages Required

1 page

Requirements
Must have
• Improve the existing page at https://mervo.site/tarnovex and add the following features to it: 1. Search functionality 2. Payment process functionality 3. Application configuration 4. Activation of registration functionality 5. Chat functionality 6. Language switching functionality (Portuguese & French) 7. Bespoke interactive modules 8. Automated web scraping and data synchronisation mechanisms 9. News Page

```html
<!DOCTYPE html>
<html lang="en">
<head>
<meta charset="utf-8">
<title>Tarnovex – Mozambique Oil &amp; Gas Intelligence</title>
<link href="https://fonts.googleapis.com/css2?family=IBM+Plex+Sans:wght@500;600;700&family=Inter:wght@400;500;600;700&display=swap" rel="stylesheet">
<style>
:root{
  --navy:#17122f;
  --navy-2:#201a3d;
  --orange:#e8521f;
  --amber:#f4a23a;
  --beige:#f1ede5;
  --white:#ffffff;
  --ink:#1b1833;
  --muted:#4a4760;
  --grad:linear-gradient(90deg,#e4461e 0%,#ef7a2a 55%,#f5a63c 100%);
}
*{box-sizing:border-box;margin:0;padding:0}
html,body{width:1200px;height:5098px;overflow:hidden}
body{font-family:"Inter",sans-serif;color:var(--ink);background:var(--beige);position:relative}
.abs{position:absolute}
h1,h2,h3{font-family:"IBM Plex Sans",sans-serif;font-weight:600}
.btn{position:absolute;display:flex;align-items:center;justify-content:center;font-size:11px;font-weight:600;letter-spacing:.2px;text-transform:uppercase;height:40px}
.btn-orange{background:var(--orange);color:#fff}
.btn-grad{background:var(--grad);color:var(--navy)}
.btn-outline-light{border:1.5px solid #fff;color:#fff}
.btn-navy{background:var(--navy);color:#fff}
.btn-outline-dark{border:1.5px solid var(--navy);color:var(--navy)}
.gears{position:absolute;width:30px;height:26px}
.section-title{position:absolute;left:0;width:1200px;text-align:center;font-size:35px;color:var(--ink)}

/* header */
.site-header{position:absolute;top:0;left:0;width:1200px;height:113px;background:#f4f2ee}
.topbar{position:absolute;left:565px;top:0;width:635px;height:40px;background:var(--navy);color:#fff;font-size:11px}
.topbar .mail{position:absolute;left:80px;top:13px}
.topbar .lang{position:absolute;left:280px;top:13px}
.topbar .lang b{color:var(--orange);font-weight:500}
.topbar .register{position:absolute;left:425px;top:0;width:92px;height:40px;background:var(--orange);color:var(--navy);font-weight:600;display:flex;align-items:center;justify-content:center}
.brand-tab{position:absolute;left:100px;top:0;width:228px;height:136px;background:#fff;z-index:3;box-shadow:0 2px 6px rgba(0,0,0,.08);display:flex;flex-direction:column;align-items:center;justify-content:center;gap:8px}
.brand-tab .dot{width:40px;height:40px;border-radius:50%;background:var(--navy)}
.brand-tab .name{font-family:"IBM Plex Sans",sans-serif;font-weight:700;font-size:20px;color:var(--navy)}
.main-nav{position:absolute;top:69px;left:384px;display:flex;gap:20px;font-size:12px;color:var(--ink)}

/* hero */
.hero{position:absolute;top:113px;left:0;width:1200px;height:580px;background:linear-gradient(100deg,#120e14 0%,#2a1d18 40%,#5b3a22 62%,#b4531f 80%,#3a2a22 100%)}
.hero-shade{position:absolute;inset:0;background:linear-gradient(90deg,rgba(12,10,20,.85) 0%,rgba(12,10,20,.5) 45%,rgba(0,0,0,0) 70%)}
.hero h1{position:absolute;left:119px;top:138px;width:470px;font-size:36px;line-height:46px;color:#fff;font-weight:500}
.hero h1 span{color:var(--amber)}
.hero p{position:absolute;left:119px;top:302px;width:470px;font-size:13px;line-height:24px;color:#fff}
.stats{position:absolute;left:109px;top:693px;width:982px;height:135px;background:var(--grad);z-index:2}
.stats-back{position:absolute;left:103px;top:713px;width:82px;height:122px;background:var(--navy);z-index:1}
.stats-corner{position:absolute;left:1012px;top:687px;width:79px;height:14px;background:#fff;z-index:1}
.stat{position:absolute;top:40px;display:flex;align-items:center;gap:14px;color:#fff}
.stat .ic{width:54px;height:54px;border-radius:50%;background:var(--navy);display:flex;align-items:center;justify-content:center}
.stat strong{display:block;font-family:"IBM Plex Sans",sans-serif;font-size:21px;font-weight:600}
.stat small{font-size:11px}

/* about */
.about-photo{position:absolute;left:122px;top:928px;width:448px;height:448px;border-radius:50%;background:radial-gradient(circle at 50% 40%,#c9905e 0%,#6d6672 45%,#2f3348 100%)}
.about h2{position:absolute;left:649px;top:1000px;font-size:34px}
.about p{position:absolute;left:649px;width:430px;font-size:13px;line-height:24px;color:var(--muted)}

/* features */
.features{position:absolute;top:1475px;left:0;width:1200px;height:970px;background:#fff}
.card{position:absolute;width:233px;height:273px;background:var(--beige);text-align:center;padding:20px 16px}
.card .ic{width:62px;height:62px;border-radius:50%;background:var(--navy);margin:0 auto 30px;display:flex;align-items:center;justify-content:center}
.card h3{font-family:"Inter",sans-serif;font-size:13px;font-weight:600;line-height:24px;color:var(--ink);margin-bottom:24px;min-height:48px;display:flex;align-items:flex-start;justify-content:center}
.card p{font-size:12.5px;line-height:24px;color:var(--muted)}
.card.dark{background:var(--navy)}
.card.dark h3,.card.dark p{color:#fff}
.card.dark .ic{background:var(--amber)}

/* how */
.how{position:absolute;top:2445px;left:0;width:1200px;height:762px;background:var(--navy)}
.how .section-title{color:#fff}
.step{position:absolute;width:140px;height:140px}
.step .diamond{position:absolute;left:20px;top:20px;width:100px;height:100px;background:#fff;transform:rotate(45deg);border:5px solid #cfcfd8;border-radius:6px}
.step .glyph{position:absolute;left:45px;top:45px;width:50px;height:50px}
.step-label{position:absolute;width:240px;text-align:center;color:#fff;font-size:13px;font-weight:600}

/* unique */
.unique-title{top:3352px}
.ring{position:absolute;width:300px;height:300px}
.ring-text{position:absolute;width:210px;text-align:center}
.ring-text h3{font-family:"Inter",sans-serif;font-size:13px;font-weight:600;line-height:24px;margin:10px 0 14px}
.ring-text p{font-size:12.5px;line-height:24px;color:var(--muted)}

/* audience */
.audience{position:absolute;top:3841px;left:0;width:1200px;height:620px;background:#fff}
.aud-card{position:absolute;top:210px;width:305px;height:295px;background:#fff;box-shadow:0 4px 18px rgba(0,0,0,.08)}
.aud-card .photo{width:305px;height:177px}
.aud-card .badge{position:absolute;right:22px;top:150px;width:54px;height:54px;border-radius:50%;display:flex;align-items:center;justify-content:center}
.aud-card h3{font-family:"Inter",sans-serif;font-size:13px;font-weight:600;margin:20px 22px 16px}
.aud-card p{font-size:12.5px;line-height:24px;color:var(--muted);margin:0 22px}

/* cta & footer */
.footer-band{position:absolute;top:4722px;left:0;width:1200px;height:376px;background:var(--navy)}
.cta{position:absolute;left:127px;top:4465px;width:952px;height:365px;background:var(--grad);text-align:center}
.cta h2{position:absolute;top:94px;left:0;width:952px;font-size:35px;line-height:48px;color:var(--navy)}
.cta p{position:absolute;top:196px;left:0;width:952px;font-size:13px;font-weight:600;line-height:24px;color:var(--navy)}
.foot-col{position:absolute;top:4884px;font-size:11px;line-height:16px;color:#fff}
.foot-col h4{font-weight:500;color:var(--orange);font-size:11px}
.copyright{position:absolute;left:133px;top:5022px;font-size:11px;color:#fff}
.social{position:absolute;top:5024px;width:14px;height:14px;border-radius:50%;background:#fff}
.chat-fab{position:absolute;left:1090px;top:4868px;width:38px;height:38px;border-radius:50%;background:#e63b35;display:flex;align-items:center;justify-content:center}
</style>
</head>
<body>

<header class="site-header">
  <div class="topbar">
    <span class="mail">✉&nbsp; contacto@tarnovexmz.org</span>
    <span class="lang">◎&nbsp; <b>EN</b> | PT | FR</span>
    <span class="register">REGISTER</span>
  </div>
  <nav class="main-nav">
    <span>Home</span><span>Industry Insights</span><span>Oil &amp; Gas Opportunities</span><span>Supplier &amp; Company Network</span><span>News</span><span>Legal Framework</span>
    <svg width="14" height="14" viewBox="0 0 14 14"><circle cx="6" cy="6" r="4.5" fill="none" stroke="#1b1833" stroke-width="1.4"/><line x1="9.5" y1="9.5" x2="13" y2="13" stroke="#1b1833" stroke-width="1.4"/></svg>
  </nav>
</header>
<div class="brand-tab"><span class="dot"></span><span class="name">Tarnovex</span></div>

<section class="hero">
  <div class="abs" role="img" aria-label="Engineer in hard hat and safety vest holding a tablet at a refinery" style="inset:0"></div>
  <div class="hero-shade"></div>
  <h1>Access Mozambique’s <span>Oil &amp; Gas Industry</span> Intelligence in One Platform</h1>
  <p>Tarnovex is a modern online connection and consulting platform designed to facilitate access to the Mozambican Oil and Gas industry through premium industry insights, supplier information, tenders, legal frameworks, and strategic project data.</p>
  <span class="btn btn-grad" style="left:119px;top:429px;width:152px">Explore Platform</span>
  <span class="btn btn-outline-light" style="left:283px;top:429px;width:147px">Become a Member</span>
</section>
<div class="stats-back"></div>
<div class="stats-corner"></div>
<div class="stats">
  <div class="stat" style="left:48px"><span class="ic"><svg width="26" height="26" viewBox="0 0 26 26" fill="none" stroke="#fff" stroke-width="1.6"><circle cx="13" cy="9" r="4"/><path d="M5 22c0-5 4-8 8-8s8 3 8 8"/></svg></span><div><strong>1,250+</strong><small>Registered Members</small></div></div>
  <div class="stat" style="left:282px"><span class="ic"><svg width="26" height="26" viewBox="0 0 26 26" fill="none" stroke="#fff" stroke-width="1.6"><rect x="6" y="4" width="14" height="18"/><path d="M10 9h2M14 9h2M10 13h2M14 13h2M11 22v-4h4v4"/></svg></span><div><strong>850+</strong><small>Companies Listed</small></div></div>
  <div class="stat" style="left:516px"><span class="ic"><svg width="26" height="26" viewBox="0 0 26 26" fill="none" stroke="#fff" stroke-width="1.6"><rect x="6" y="4" width="13" height="18" rx="1"/><path d="M9 9h7M9 13h7M9 17h4"/></svg></span><div><strong>350+</strong><small>Industry Reports</small></div></div>
  <div class="stat" style="left:750px"><span class="ic"><svg width="26" height="26" viewBox="0 0 26 26" fill="none" stroke="#fff" stroke-width="1.6"><circle cx="13" cy="13" r="9"/><path d="M4 13h18M13 4c3 3 3 15 0 18M13 4c-3 3-3 15 0 18"/></svg></span><div><strong>80+</strong><small>Countries Represented</small></div></div>
</div>

<section class="about">
  <div class="about-photo" role="img" aria-label="Refinery towers lit at dusk"></div>
  <svg class="gears" style="left:649px;top:962px" viewBox="0 0 30 26"><circle cx="10" cy="16" r="6" fill="none" stroke="#e8521f" stroke-width="3"/><circle cx="22" cy="7" r="4" fill="none" stroke="#f4a23a" stroke-width="2.5"/></svg>
  <h2>What is Tarnovex?</h2>
  <p style="top:1066px">Tarnovex is a unique online platform built to connect businesses, investors, suppliers, and professionals with valuable information about the Mozambican Oil &amp; Gas sector.</p>
  <p style="top:1162px">Through a secure digital paywall system, users gain access to organized, up-to-date, and carefully selected industry information that supports better decision-making, market understanding, and business opportunities within Mozambique’s growing hydrocarbons industry.</p>
  <span class="btn btn-orange" style="left:649px;top:1301px;width:147px;color:var(--navy)">Explore Services</span>
</section>

<section class="features">
  <svg class="gears" style="left:585px;top:96px" viewBox="0 0 30 26"><circle cx="10" cy="16" r="6" fill="none" stroke="#e8521f" stroke-width="3"/><circle cx="22" cy="7" r="4" fill="none" stroke="#f4a23a" stroke-width="2.5"/></svg>
  <h2 class="section-title" style="top:128px">Everything You Need in One Place</h2>
  <div class="card" style="left:216px;top:212px"><div class="ic"><svg width="30" height="30" viewBox="0 0 30 30" fill="none" stroke="#fff" stroke-width="1.6"><circle cx="15" cy="15" r="4"/><path d="M15 4v7M15 19v7M4 15h7M19 15h7M7 7l5 5M18 18l5 5M23 7l-5 5M12 18l-5 5"/></svg></div><h3>Hydrocarbon Industry Information</h3><p>General information and insights about Mozambique’s oil and gas sector.</p></div>
  <div class="card dark" style="left:483px;top:212px"><div class="ic"><svg width="30" height="30" viewBox="0 0 30 30" fill="none" stroke="#17122f" stroke-width="1.8"><path d="M8 25h14M11 25l4-16 4 16M6 9h18M15 5v4"/></svg></div><h3>Main Gas Projects</h3><p>Details about major gas and energy projects operating in Mozambique.</p></div>
  <div class="card" style="left:752px;top:212px"><div class="ic"><svg width="30" height="30" viewBox="0 0 30 30" fill="none" stroke="#fff" stroke-width="1.6"><path d="M5 15l6-5 4 3 4-3 6 5-8 7z"/></svg></div><h3>Supplier &amp; Company Database</h3><p>Mozambican companies capable of meeting Level 3 supply requirements.</p></div>
  <div class="card" style="left:216px;top:515px"><div class="ic"><svg width="30" height="30" viewBox="0 0 30 30" fill="none" stroke="#fff" stroke-width="1.6"><rect x="5" y="8" width="20" height="14"/><path d="M5 8l10 8 10-8"/></svg></div><h3>Industry Contacts</h3><p>Key contacts from NOCs, Operators, EPCs, and Second-Tier Suppliers.</p></div>
  <div class="card" style="left:483px;top:515px"><div class="ic"><svg width="30" height="30" viewBox="0 0 30 30" fill="none" stroke="#fff" stroke-width="1.6"><rect x="8" y="5" width="14" height="20" rx="1"/><path d="M11 11h8M11 15h8M11 19h5"/></svg></div><h3>Tender Opportunities</h3><p>Short, medium, and long-term tenders within the industry.</p></div>
  <div class="card" style="left:752px;top:515px"><div class="ic"><svg width="30" height="30" viewBox="0 0 30 30" fill="none" stroke="#fff" stroke-width="1.6"><circle cx="11" cy="15" r="4"/><path d="M15 15h11M22 15v4M25 15v3"/></svg></div><h3>Ownership &amp; Access</h3><p>Information related to hydrocarbon reserves and sector participation.</p></div>
  <span class="btn btn-grad" style="left:538px;top:831px;width:123px">Explore More</span>
</section>

<section class="how">
  <svg class="gears" style="left:585px;top:90px" viewBox="0 0 30 26"><circle cx="10" cy="16" r="6" fill="none" stroke="#e8521f" stroke-width="3"/><circle cx="22" cy="7" r="4" fill="none" stroke="#f4a23a" stroke-width="2.5"/></svg>
  <h2 class="section-title" style="top:124px;font-size:35px">How the Platform Works</h2>
  <svg class="abs" style="left:0;top:0" width="1200" height="762" viewBox="0 0 1200 762" fill="none" stroke="#fff" stroke-width="2">
    <circle cx="119" cy="287" r="5" fill="#fff"/>
    <path d="M119 287H1066a15 15 0 0 1 15 15v218a15 15 0 0 1-15 15H124"/>
    <path d="M134 527l-12 8 12 8" />
  </svg>
  <div class="step" style="left:191px;top:217px"><div class="diamond"></div><svg class="glyph" viewBox="0 0 50 50" fill="none" stroke="#17122f" stroke-width="2"><rect x="12" y="8" width="20" height="28" rx="2"/><path d="M16 16h12M16 22h8"/><circle cx="33" cy="34" r="7"/><path d="M30 34l2 2 4-4"/></svg></div>
  <div class="step" style="left:502px;top:217px"><div class="diamond"></div><svg class="glyph" viewBox="0 0 50 50" fill="none" stroke="#17122f" stroke-width="2"><rect x="10" y="12" width="30" height="24" rx="2"/><circle cx="25" cy="21" r="4"/><path d="M18 32c2-4 12-4 14 0"/></svg></div>
  <div class="step" style="left:815px;top:217px"><div class="diamond"></div><svg class="glyph" viewBox="0 0 50 50" fill="none" stroke="#17122f" stroke-width="2"><path d="M10 22l15-8 15 8-15 8z"/><path d="M10 22v10l15 8 15-8V22"/><circle cx="25" cy="12" r="5"/></svg></div>
  <div class="step" style="left:348px;top:465px"><div class="diamond"></div><svg class="glyph" viewBox="0 0 50 50" fill="none" stroke="#17122f" stroke-width="2"><path d="M10 38h30M14 38V30M20 38V26M26 38V22M32 38V18"/><circle cx="24" cy="12" r="5"/></svg></div>
  <div class="step" style="left:659px;top:465px"><div class="diamond"></div><svg class="glyph" viewBox="0 0 50 50" fill="none" stroke="#17122f" stroke-width="2"><path d="M25 10l14 7-14 7-14-7z"/><path d="M11 24l14 7 14-7M11 31l14 7 14-7"/></svg></div>
  <div class="step-label" style="left:141px;top:390px">Register Securely</div>
  <div class="step-label" style="left:452px;top:390px">Subscribe Securely</div>
  <div class="step-label" style="left:765px;top:390px">Unlock Premium Access</div>
  <div class="step-label" style="left:298px;top:640px">Grow with Confidence</div>
  <div class="step-label" style="left:609px;top:640px">Explore the Platform</div>
</section>

<section class="unique">
  <svg class="gears" style="left:585px;top:3318px" viewBox="0 0 30 26"><circle cx="10" cy="16" r="6" fill="none" stroke="#e8521f" stroke-width="3"/><circle cx="22" cy="7" r="4" fill="none" stroke="#f4a23a" stroke-width="2.5"/></svg>
  <h2 class="section-title unique-title">Why Tarnovex Is Unique</h2>
  <svg class="ring" style="left:147px;top:3434px" viewBox="0 0 300 300" fill="none" stroke-width="7" stroke-linecap="round"><circle cx="150" cy="150" r="128" fill="#fff" stroke="none"/><path d="M58.7 258.8A142 142 0 1 1 266.3 231.5" stroke="#17122f"/></svg>
  <svg class="ring" style="left:450px;top:3434px" viewBox="0 0 300 300" fill="none" stroke-width="7" stroke-linecap="round"><circle cx="150" cy="150" r="128" fill="#fff" stroke="none"/><path d="M33.7 231.5A142 142 0 0 1 58.7 41.2" stroke="#e8521f"/><path d="M231.5 33.7A142 142 0 0 1 273 221" stroke="#e8521f"/><path d="M231.5 266.3A142 142 0 0 1 68.5 266.3" stroke="#e8521f"/></svg>
  <svg class="ring" style="left:751px;top:3434px" viewBox="0 0 300 300" fill="none" stroke-width="7" stroke-linecap="round"><circle cx="150" cy="150" r="128" fill="#fff" stroke="none"/><path d="M27 221A142 142 0 1 1 198.6 283.4" stroke="#17122f"/></svg>
  <div class="ring-text" style="left:192px;top:3466px"><svg width="40" height="36" viewBox="0 0 40 36" fill="none" stroke="#17122f" stroke-width="1.6"><circle cx="20" cy="18" r="12"/><path d="M14 18h12M20 12v12"/></svg><h3>Up-to-Date Industry Intelligence</h3><p>Receive frequent updates about developments in Mozambique’s Oil &amp; Gas sector.</p></div>
  <div class="ring-text" style="left:495px;top:3466px"><svg width="40" height="36" viewBox="0 0 40 36" fill="none" stroke="#17122f" stroke-width="1.6"><rect x="8" y="8" width="24" height="20"/><path d="M12 14h16M12 19h16M12 24h10"/></svg><h3>High-Quality Curated Information</h3><p>Access carefully selected and synthesized information tailored to industry stakeholders.</p></div>
  <div class="ring-text" style="left:796px;top:3466px"><svg width="40" height="36" viewBox="0 0 40 36" fill="none" stroke="#17122f" stroke-width="1.6"><circle cx="18" cy="18" r="11"/><path d="M18 11v7l5 3"/><circle cx="30" cy="27" r="5"/></svg><h3>Time-Saving Access</h3><p>Avoid spending hours searching through scattered online sources with organized and accessible content in one platform.</p></div>
</section>

<section class="audience">
  <svg class="gears" style="left:585px;top:108px" viewBox="0 0 30 26"><circle cx="10" cy="16" r="6" fill="none" stroke="#e8521f" stroke-width="3"/><circle cx="22" cy="7" r="4" fill="none" stroke="#f4a23a" stroke-width="2.5"/></svg>
  <h2 class="section-title" style="top:140px">Who Is It For?</h2>
  <svg class="abs" style="left:52px;top:315px" width="58" height="16" viewBox="0 0 58 16" fill="none" stroke="#17122f" stroke-width="1.6"><path d="M56 8H3M10 2L3 8l7 6"/></svg>
  <svg class="abs" style="left:1098px;top:315px" width="58" height="16" viewBox="0 0 58 16" fill="none" stroke="#17122f" stroke-width="1.6"><path d="M2 8h53M48 2l7 6-7 6"/></svg>
  <div class="aud-card" style="left:121px"><div class="photo" role="img" aria-label="Investors meeting around a table" style="background:linear-gradient(135deg,#6b5a4c,#2f2c35)"></div><span class="badge" style="background:var(--navy)"><svg width="24" height="24" viewBox="0 0 24 24" fill="none" stroke="#fff" stroke-width="1.6"><circle cx="12" cy="9" r="4"/><path d="M5 20c1-4 13-4 14 0"/></svg></span><h3>Investors</h3><p>Evaluate opportunities with reliable market intelligence.</p></div>
  <div class="aud-card" style="left:448px"><div class="photo" role="img" aria-label="Yellow hard hat resting on engineering documents" style="background:linear-gradient(135deg,#f0b23a,#5a5550)"></div><span class="badge" style="background:var(--orange)"><svg width="24" height="24" viewBox="0 0 24 24" fill="none" stroke="#fff" stroke-width="1.6"><path d="M4 20h16M6 20V10h4v10M14 20V6h4v14"/></svg></span><h3>EPC Contractors</h3><p>Connect with qualified local businesses.</p></div>
  <div class="aud-card" style="left:774px"><div class="photo" role="img" aria-label="Domed government building at dusk" style="background:linear-gradient(180deg,#4d6aa8,#1e2a4c)"></div><span class="badge" style="background:var(--navy)"><svg width="24" height="24" viewBox="0 0 24 24" fill="none" stroke="#fff" stroke-width="1.6"><path d="M3 9l9-5 9 5zM5 9v9M9 9v9M15 9v9M19 9v9M3 20h18"/></svg></span><h3>Government Agencies</h3><p>Access industry information that supports planning and development.</p></div>
</section>

<div class="footer-band"></div>
<section class="cta">
  <svg class="gears" style="left:461px;top:52px" viewBox="0 0 30 26"><circle cx="10" cy="16" r="6" fill="none" stroke="#17122f" stroke-width="3"/><circle cx="22" cy="7" r="4" fill="none" stroke="#17122f" stroke-width="2.5"/></svg>
  <h2>Start Exploring Mozambique’s Oil &amp;<br>Gas Opportunities</h2>
  <p>Register today to access premium industry information, supplier networks,<br>tenders, and strategic market insights through Tarnovex.</p>
  <span class="btn btn-navy" style="left:350px;top:271px;width:125px">Register Now</span>
  <span class="btn btn-outline-dark" style="left:489px;top:271px;width:109px">Contact Us</span>
</section>

<footer>
  <div class="foot-col" style="left:164px"><h4>Explore</h4>Courses<br>Learning Paths<br>Certifications<br>Industry News<br>Resources</div>
  <div class="foot-col" style="left:341px"><h4>Solutions</h4>Individual Learning<br>Corporate Training<br>Enterprise Solutions<br>Government Programs</div>
  <div class="foot-col" style="left:558px"><h4>Support</h4>Help Centre<br>FAQs<br>Contact Us</div>
  <div class="foot-col" style="left:733px"><h4>Company</h4>About Tarnovex<br>Careers<br>Partners<br>Newsroom</div>
  <div class="foot-col" style="left:917px"><h4>Legal</h4>Privacy Policy<br>Terms &amp; Conditions<br>Cookie Policy<br>Accessibility</div>
  <div class="copyright">Copyright@2026.All Rights Reserved.</div>
  <span class="social" style="left:988px"></span>
  <span class="social" style="left:1020px"></span>
  <span class="social" style="left:1052px"></span>
  <span class="chat-fab"><svg width="20" height="18" viewBox="0 0 20 18" fill="none" stroke="#fff" stroke-width="1.8"><path d="M2 3h16v10H8l-4 3v-3H2z"/></svg></span>
</footer>

</body>
</html>
```